Webdesign für Brenner Flusskraft
Zielgruppe
Ansprechpartner für Planung und Errichtung von Stromerzeugung durch erneuerbare Energien. Alle Interessen im privaten, teilöffentlichen und öffentlichen Bereich, die mittel- und langfristig umweltschonenden Strom nutzen wollen.
Aufgabenstellung
- Farben bitte in den Unternehmensfarben Blau/Weiß mit einem kleinen Anteil Orange
- Bilder nach Möglichkeit bitte nur eigene (siehe Anhang)
- klare und übersichtliche Struktur
- KEIN Abklatsch der alten Webseite

```html
<!DOCTYPE html>
<html lang="de">
<head>
<meta charset="utf-8">
<title>Brenner Flusskraft</title>
<link href="https://fonts.googleapis.com/css2?family=Inter:wght@400;500;600;700;800&display=swap" rel="stylesheet">
<style>
  :root {
    --brand-blue: #1b80b9;
    --deep-navy: #0c3250;
    --text-blue: #3f94c9;
    --link-blue: #a9d2ec;
    --white: #ffffff;
    --photo-sky: #8fb3c9;
    --photo-roof: #b9c4cc;
  }
  * { margin: 0; padding: 0; box-sizing: border-box; }
  html, body { width: 1200px; height: 1061px; overflow: hidden; background: var(--white); }
  body { position: relative; font-family: "Inter", sans-serif; }

  .top-band { position: absolute; left: 0; top: 0; width: 1200px; height: 358px; background: var(--brand-blue); }

  .brand { position: absolute; left: 88px; top: 47px; display: flex; align-items: center; gap: 7px;
    color: var(--white); font-weight: 700; font-size: 14px; }
  .brand-dot { width: 22px; height: 22px; border-radius: 50%; border: 2px solid var(--white); }

  .main-nav a { position: absolute; top: 36px; color: var(--white); font-size: 12.5px; font-weight: 600;
    text-decoration: none; letter-spacing: -0.2px; }

  .hero-panel { position: absolute; left: 88px; top: 122px; width: 1025px; height: 367px; background: var(--deep-navy); }
  .hero-title { position: absolute; left: 36px; top: 50px; color: var(--white); font-size: 38px; font-weight: 800;
    line-height: 44px; letter-spacing: -0.8px; }
  .hero-text { position: absolute; left: 36px; width: 320px; color: var(--text-blue); font-size: 12px;
    line-height: 20px; letter-spacing: -0.1px; }
  .hero-text.first { top: 160px; }
  .hero-text.second { top: 226px; }
  .hero-link { position: absolute; left: 36px; top: 314px; color: var(--link-blue); font-size: 12.5px;
    font-weight: 700; text-decoration: none; }
  .hero-photo { position: absolute; left: 388px; top: 7px; width: 627px; height: 352px;
    background: linear-gradient(180deg, var(--photo-sky) 0%, #a9c6d6 40%, #5f8a5a 48%, var(--photo-roof) 56%, #aeb9c0 100%); }

  .company-photo { position: absolute; left: 88px; top: 612px; width: 474px; height: 352px;
    background: linear-gradient(180deg, var(--photo-sky) 0%, #a9c6d6 40%, #5f8a5a 48%, var(--photo-roof) 56%, #aeb9c0 100%); }
  .company-photo-strip { position: absolute; left: 561px; top: 902px; width: 153px; height: 63px;
    background: linear-gradient(180deg, #b9c4cc, #aeb9c0); }

  .company-title { position: absolute; left: 600px; top: 632px; color: var(--deep-navy); font-size: 38px;
    font-weight: 700; letter-spacing: -0.8px; }
  .company-text { position: absolute; left: 608px; width: 470px; color: var(--deep-navy); font-size: 12px;
    line-height: 20px; letter-spacing: -0.1px; }
  .company-text.first { top: 694px; }
  .company-text.second { top: 788px; }
</style>
</head>
<body>
  <div class="top-band"></div>

  <div class="brand"><span class="brand-dot"></span>Brenner Flusskraft</div>

  <nav class="main-nav">
    <a href="#" style="left:476px">Home</a>
    <a href="#" style="left:561px">Unternehmen</a>
    <a href="#" style="left:688px">Leistungen</a>
    <a href="#" style="left:804px">Referenzen</a>
    <a href="#" style="left:1040px">Kontakt</a>
  </nav>

  <section class="hero-panel">
    <h1 class="hero-title">TECHNOLOGY<br>SOLAR ENERGY</h1>
    <p class="hero-text first">In unserer Firma betreiben wir 5 Wasserkraftanlagen und haben die tägliche Wartung von kundeneigenen Wasserkraftanlagen übernommen.</p>
    <p class="hero-text second">In unseren Steuerungen verwenden wir durchgängig Komponenten deutscher Hersteller und können mit einer sehr guten Ersatzteilverfügbarkeit im Fehlerfall schnelle Abhilfe schaffen.</p>
    <a class="hero-link" href="#">Mehr Erfahren</a>
    <div class="hero-photo" role="img" aria-label="Monteur beim Aufbau einer Solaranlage auf einem Hallendach unter blauem Himmel"></div>
  </section>

  <div class="company-photo" role="img" aria-label="Solarmodule und Montageschienen auf einem Industriedach mit Monteur"></div>
  <div class="company-photo-strip" role="img" aria-label="Dachfläche mit Montageschienen"></div>

  <h2 class="company-title">Unternehmen</h2>
  <p class="company-text first">In unserer Firma betreiben wir 5 Wasserkraftanlagen und haben die tägliche Wartung von kundeneigenen Wasserkraftanlagen übernommen.<br>In unserer Firma betreiben wir 5 Wasserkraftanlagen und haben die tägliche Wartung von kundeneigenen Wasserkraftanlagen übernommen.</p>
  <p class="company-text second">In unserer Firma betreiben wir 5 Wasserkraftanlagen und haben die tägliche Wartung von kundeneigenen Wasserkraftanlagen übernommen.<br>In unserer Firma betreiben wir 5 Wasserkraftanlagen und haben die tägliche Wartung von kundeneigenen Wasserkraftanlagen übernommen.</p>
</body>
</html>
```